Law Firm Folder with 5 step inserts

Square Corners Two Pocket Presentation Folder - inside and outside design with 5 stepped inserts. Please look at website pelvaninjurylaw .com for colors

Target Market(s)

Given to new clients

Industry/Entity Type

legal

Requirements
Must have
• use brand colors.
Nice to have
• would like to include partner photos
Should not have
• not generic

```html
<!DOCTYPE html>
<html lang="en">
<head>
<meta charset="utf-8">
<title>Pelvan Restrepo – Presentation Folder Spread</title>
<link rel="stylesheet" href="https://fonts.googleapis.com/css2?family=Arimo:wght@400;700&family=Roboto+Condensed:wght@300;700&display=swap">
<style>
  :root {
    --navy-deep: #0f1a2e;
    --navy: #1c2c47;
    --navy-light: #31496b;
    --slate: #3a4f6c;
    --gold: #d4a72c;
    --gold-light: #f1d46a;
    --white: #ffffff;
    --ink: #1b2233;
    --muted: #c9d3e0;
    --backdrop: #7e8786;
  }
  * { box-sizing: border-box; margin: 0; padding: 0; }
  html, body { width: 1200px; height: 900px; overflow: hidden; }
  body {
    background: var(--backdrop);
    font-family: "Arimo", Arial, sans-serif;
    color: var(--white);
    position: relative;
  }
  .folder-spread {
    position: absolute; left: 30px; top: 70px;
    width: 1140px; height: 760px;
    display: flex;
    box-shadow: 0 18px 40px rgba(0,0,0,.35);
  }
  .panel {
    position: relative; width: 570px; height: 760px; overflow: hidden;
    border-top: 6px solid var(--gold);
    border-bottom: 6px solid var(--gold);
  }
  .panel-left {
    border-left: 6px solid var(--gold);
    background: linear-gradient(160deg, var(--navy-light) 0%, var(--navy) 45%, var(--navy-deep) 100%);
  }
  .panel-right {
    border-right: 6px solid var(--gold);
    background: linear-gradient(180deg, var(--slate) 0%, var(--navy) 55%, var(--navy-deep) 100%);
  }

  /* Left panel */
  .team-photo {
    position: absolute; left: 24px; top: 20px; width: 516px; height: 210px;
    background: linear-gradient(135deg, #caa675 0%, #8b4a2c 45%, #3d2a22 75%, #e5e0d6 100%);
  }
  .content-frame {
    position: absolute; left: 40px; top: 246px; width: 484px; height: 314px;
    border: 1px solid var(--gold);
  }
  .intro-title {
    position: absolute; left: 24px; top: 235px; width: 516px; text-align: center; line-height: 22px;
  }
  .intro-title span { background: #1f3050; padding: 0 12px; font-weight: 700; font-size: 18px; }
  .intro-body {
    position: absolute; left: 60px; top: 270px; width: 444px;
    font-size: 10.5px; line-height: 1.45; color: var(--muted);
  }
  .intro-body p { margin-bottom: 9px; }
  .client-list { list-style: none; margin: 2px 0 9px; }
  .client-list li { display: flex; align-items: center; gap: 7px; font-size: 11px; line-height: 1.5; color: var(--white); }
  .tick { width: 11px; height: 9px; flex: none; }
  .locations-title {
    position: absolute; left: 24px; top: 549px; width: 516px; text-align: center; line-height: 22px;
  }
  .locations-title span { background: #17263f; padding: 0 12px; font-weight: 700; font-size: 18px; }
  .locations-lede {
    position: absolute; left: 80px; top: 578px; width: 404px;
    font-size: 10px; line-height: 1.4; color: var(--muted); text-align: center;
  }
  .location-grid {
    position: absolute; left: 56px; top: 620px; width: 452px;
    display: grid; grid-template-columns: 1fr 1fr; gap: 8px 24px;
  }
  .location-tab {
    height: 20px; background: #24375a; font-size: 12px; font-weight: 700;
    display: flex; align-items: center; justify-content: center;
    box-shadow: 0 3px 6px rgba(0,0,0,.45);
  }

  /* Right panel */
  .brand {
    position: absolute; left: 30px; top: 28px; display: flex; align-items: center; gap: 10px;
  }
  .brand-dot { width: 30px; height: 30px; border-radius: 50%; background: var(--gold); }
  .brand-name { font-size: 17px; font-weight: 700; line-height: 1.05; letter-spacing: 1px; color: var(--white); }
  .partners-photo {
    position: absolute; left: 190px; top: 40px; width: 370px; height: 380px;
    background: radial-gradient(ellipse at 55% 35%, #5e7397 0%, #2a3d64 55%, #1c2c47 100%);
  }
  .partner-label { position: absolute; font-family: "Roboto Condensed", Arial, sans-serif; }
  .partner-name { font-weight: 700; font-size: 15px; line-height: 1.1; color: var(--white); }
  .partner-role { font-weight: 300; font-size: 9px; line-height: 1.25; color: var(--muted); letter-spacing: .6px; text-transform: uppercase; margin-top: 4px; }
  .partner-a { left: 40px; top: 240px; }
  .partner-b { right: 22px; top: 60px; text-align: right; }

  .chevron { position: absolute; left: 0; top: 348px; width: 558px; height: 160px; }
  .tagline-band {
    position: absolute; left: 0; top: 418px; width: 558px; height: 112px;
    background: var(--navy-deep);
  }
  .tagline {
    position: absolute; left: 26px; top: 14px;
    font-size: 21px; font-weight: 700; color: var(--white);
  }
  .guarantee-list { position: absolute; left: 26px; top: 50px; list-style: none; }
  .guarantee-list li { display: flex; align-items: center; gap: 6px; font-size: 7.5px; line-height: 1.7; color: var(--muted); }
  .guarantee-mark { position: absolute; right: 24px; top: 12px; display: flex; align-items: center; gap: 10px; }
  .guarantee-word { font-size: 13px; line-height: 1.15; text-align: right; color: var(--white); }
  .guarantee-seal { width: 52px; height: 52px; border-radius: 50%; background: radial-gradient(circle, var(--gold-light), var(--gold)); border: 2px solid #8a6a12; }

  .info-area {
    position: absolute; left: 0; top: 530px; width: 558px; height: 218px;
    background: var(--white); color: var(--ink);
  }
  .awards { position: absolute; left: 140px; top: 12px; display: flex; gap: 10px; }
  .award-card { width: 36px; height: 36px; border: 2px solid var(--ink); background: #f3efe3; outline: 1px solid var(--gold); outline-offset: -6px; }
  .about-title { position: absolute; left: 26px; top: 54px; font-size: 19px; font-weight: 700; line-height: 22px; }
  .about-rule { position: absolute; left: 26px; top: 80px; width: 300px; height: 1px; background: var(--gold); }
  .quote-mark { position: absolute; left: 24px; top: 86px; font-size: 40px; font-weight: 700; color: var(--gold); line-height: 1; }
  .about-body { position: absolute; left: 56px; top: 90px; width: 276px; font-size: 8.5px; line-height: 1.42; color: var(--ink); }
  .contact-divider { position: absolute; left: 356px; top: 16px; width: 1px; height: 160px; background: var(--gold); }
  .contact-list { position: absolute; left: 374px; top: 24px; list-style: none; }
  .contact-list li { display: flex; align-items: center; gap: 10px; font-size: 10.5px; font-weight: 700; margin-bottom: 16px; }
  .contact-list li.phone { font-size: 14px; }
  .contact-icon { width: 18px; height: 18px; flex: none; }
</style>
</head>
<body>
  <main class="folder-spread">
    <section class="panel panel-left">
      <div class="team-photo" role="img" aria-label="Photo of the legal team meeting around a conference table"></div>
      <div class="content-frame"></div>
      <h2 class="intro-title"><span>Lorem ipsum dolor sit amet</span></h2>
      <div class="intro-body">
        <p>The legal process can be overwhelming. Too often, victims of negligence shy away from pursuing legal action even when they rightfully deserve compensation for their injuries. You may be facing pain, disability, and time away from work that you and your family simply can't afford. Our Florida injury attorneys are dedicated to understanding the unique details of your case and providing clear and honest counsel.</p>
        <p>Through care, communication, and a commitment to excellence, Pelvan &amp; Restrepo takes the stress out of your legal matters so you can focus on healing. It has been our honor to serve a variety of clients, including:</p>
        <ul class="client-list">
          <li><svg class="tick" viewBox="0 0 11 9"><path d="M1 5l3 3 6-7" fill="none" stroke="#d4a72c" stroke-width="1.6"/></svg>Drivers</li>
          <li><svg class="tick" viewBox="0 0 11 9"><path d="M1 5l3 3 6-7" fill="none" stroke="#d4a72c" stroke-width="1.6"/></svg>Property Owners</li>
          <li><svg class="tick" viewBox="0 0 11 9"><path d="M1 5l3 3 6-7" fill="none" stroke="#d4a72c" stroke-width="1.6"/></svg>Businesses</li>
          <li><svg class="tick" viewBox="0 0 11 9"><path d="M1 5l3 3 6-7" fill="none" stroke="#d4a72c" stroke-width="1.6"/></svg>Professionals</li>
          <li><svg class="tick" viewBox="0 0 11 9"><path d="M1 5l3 3 6-7" fill="none" stroke="#d4a72c" stroke-width="1.6"/></svg>Employers</li>
        </ul>
        <p>This is your case and your life. Your voice is essential to our process. We are proud to advocate on your behalf, and we will do everything within the law to obtain the justice you deserve.</p>
      </div>
      <h2 class="locations-title"><span>Out Location</span></h2>
      <p class="locations-lede">Lorem ipsum dolor sit amet, consectetuer adipiscing elit, sed diam nonummy nibh euismod tincidunt ut laoreet dolore magna aliquam erat volutpat. Ut wisi enim ad</p>
      <div class="location-grid">
        <div class="location-tab">Boca Raton</div>
        <div class="location-tab">Boyn Beach</div>
        <div class="location-tab">Delray Beach</div>
        <div class="location-tab">Ft. Lauderdale</div>
        <div class="location-tab">Palm Bay</div>
        <div class="location-tab">Stuart</div>
        <div class="location-tab">Vero Beach</div>
        <div class="location-tab">West Palm Beach</div>
      </div>
    </section>

    <section class="panel panel-right">
      <div class="partners-photo" role="img" aria-label="Portrait photo of the two founding partners in suits"></div>
      <div class="brand">
        <span class="brand-dot"></span>
        <span class="brand-name">PELVAN<br>RESTREPO</span>
      </div>
      <div class="partner-label partner-a">
        <div class="partner-name">Franklin<br>M. Restrepo</div>
        <div class="partner-role">Founding<br>Partner of<br>Pelvan &amp; Restrepo</div>
      </div>
      <div class="partner-label partner-b">
        <div class="partner-name">Warren<br>T. Pelvan</div>
        <div class="partner-role">Founding<br>Partner of<br>Pelvan &amp; Restrepo</div>
      </div>
      <svg class="chevron" viewBox="0 0 558 160" aria-hidden="true">
        <polygon points="0,20 300,70 558,0 558,160 0,160" fill="#0f1a2e"/>
        <polyline points="0,20 300,70 558,0" fill="none" stroke="#d4a72c" stroke-width="4"/>
        <polyline points="0,34 300,84 558,14" fill="none" stroke="#d4a72c" stroke-width="1"/>
      </svg>
      <div class="tagline-band">
        <h1 class="tagline">It's Not Just a Case. It's Your Life.</h1>
        <ul class="guarantee-list">
          <li><svg class="tick" viewBox="0 0 11 9"><path d="M1 5l3 3 6-7" fill="none" stroke="#d4a72c" stroke-width="1.6"/></svg>We Guarantee it's FREE if we don't get you any money.</li>
          <li><svg class="tick" viewBox="0 0 11 9"><path d="M1 5l3 3 6-7" fill="none" stroke="#d4a72c" stroke-width="1.6"/></svg>We Guarantee to guide you step-by-step through the recovery process.</li>
          <li><svg class="tick" viewBox="0 0 11 9"><path d="M1 5l3 3 6-7" fill="none" stroke="#d4a72c" stroke-width="1.6"/></svg>We Guarantee to fight to prevent the insurance companies from taking advantage of you.</li>
        </ul>
        <div class="guarantee-mark">
          <div class="guarantee-word">Our<br>Guarantee</div>
          <div class="guarantee-seal"></div>
        </div>
      </div>
      <div class="info-area">
        <div class="awards">
          <div class="award-card"></div>
          <div class="award-card"></div>
          <div class="award-card"></div>
          <div class="award-card"></div>
        </div>
        <h2 class="about-title">About Us</h2>
        <div class="about-rule"></div>
        <div class="quote-mark">&ldquo;</div>
        <p class="about-body">Lorem ipsum dolor sit amet, consectetuer adipiscing elit, sed diam nibh euismod tincidunt ut laoreet dolore magna aliquam erat volutpat. Ut wisi enim ad minim veniam, quis nostrud exerci tation ullamcorper suscipit lobortis nisl ut aliquip ex ea commodo consequat. Duis autem vel eum iriure dolor in hendrerit in vulputate velit esse molestie consequat, vel illum dolore eu feugiat nulla facilisis at vero eros et accumsan et iusto odio dignissim qui blan</p>
        <div class="contact-divider"></div>
        <ul class="contact-list">
          <li class="phone">
            <svg class="contact-icon" viewBox="0 0 18 18"><circle cx="9" cy="9" r="8" fill="none" stroke="#1b2233" stroke-width="1.3"/><path d="M6 5.5l1.6-.5 1 2.2-1 .8a5 5 0 002.4 2.4l.8-1 2.2 1-.5 1.6c-3.5.3-6.8-3-6.5-6.5z" fill="#1b2233"/></svg>
            (561) 555-0142
          </li>
          <li>
            <svg class="contact-icon" viewBox="0 0 18 18"><rect x="1.5" y="4" width="15" height="10" fill="none" stroke="#1b2233" stroke-width="1.3"/><path d="M1.5 4l7.5 6 7.5-6" fill="none" stroke="#1b2233" stroke-width="1.3"/></svg>
            Hello@PelvanInjuryLaw.com
          </li>
          <li>
            <svg class="contact-icon" viewBox="0 0 18 18"><circle cx="9" cy="9" r="7.5" fill="none" stroke="#1b2233" stroke-width="1.3"/><ellipse cx="9" cy="9" rx="3.2" ry="7.5" fill="none" stroke="#1b2233" stroke-width="1.1"/><path d="M1.5 9h15M3 5h12M3 13h12" stroke="#1b2233" stroke-width="1.1"/></svg>
            www.pelvan-restrepo.com
          </li>
        </ul>
      </div>
    </section>
  </main>
</body>
</html>
```